Coral Wing Flights brochure

A single A4 brochures that is tri-folded and shows some of our tour packages with contact details.

Please visit www.coralwingflights.com.au to see the designs and images that can be used.

I want to provide designers the freedom to try something creative because I want to give prospective client - normally tourists to Sydney a quality service. I want the brochure to reflect this.

The image on the front page needs to be of the Sydney Harbour. The image MUST be in daylight - not night time.

I have now provided an image of the aircraft (in GIF format). Please use this image and place it over the image of the sydney harbour bridge and quayside concert pavilion.

I may need to discuss this further but what I have not show in the attached files is a small form I will like the client to fill out..

Reservation number
Name
Address
Phone number
Email

We can discuss this at a latter time.

The QR Code needs to contain your web address (www.coralwingflights.com.au)

Target Market(s)

Visitors and tourists to Sydney who want a day trip.
We are providing an exciting way to see Sydney. By air in a light aircraft...

Industry/Entity Type

House

Font styles to use
Sans Serif
Script

Colors
33a6d7
3276b5
85acd3
85cae6
ffffff

Requirements
Must have
• Brochure must be A4 (with about 2 to 3mm bleed - so it can be cut at the printers). They but be folded in 3 to produce a DL size brochure.

The words "Prepare to be amazed" should be in script font...

Please use the following wording for our Terms can conditions...

Terms and Conditions
Coral Wing Flights operates from Merrowdale Airfield within Sydney’s busy airspace Your chosen flight may be subject to delays. Clearance to enter controlled airspace may be refused - this is especially true of our popular Coastline Panorama flight. If this happens, we can either offer other suitable flights, reschedule the flight or, if this isn’t suitable, we provide a refund.
Other aircraft, besides our standard Talbin Skyrunners, are available if we consider they better suit your requirements.
See our web site www.coralwingflights.com.au for full details.
Coral Wing Flights is a trading name of Orvexa Pty Limited
(ABN 81 417 286 309) which operates under the Air Operators Certificate (AOC) of Dorrigan and Welsford Pty Ltd.
Nice to have
• Suggestion - on one of the sides (with the packages) to have a background image.

Suggestion is to keep the brochure light and "airy"

```html
<!DOCTYPE html>
<html lang="en">
<head>
<meta charset="utf-8">
<title>Coral Wing Flights – Scenic Flight Packages</title>
<link rel="stylesheet" href="https://fonts.googleapis.com/css2?family=Roboto+Condensed:wght@300;400&family=Roboto:ital,wght@0,400;1,400&display=swap">
<style>
  :root{
    --backdrop:#8d8d8d;
    --panel-blue:#1f95d3;
    --panel-blue-light:#33a6d7;
    --panel-blue-deep:#1b86c6;
    --text-white:#ffffff;
    --text-soft:#e4f3fb;
    --shade:rgba(5,12,30,0.78);
  }
  *{margin:0;padding:0;box-sizing:border-box}
  html,body{width:1200px;height:911px;overflow:hidden;background:var(--backdrop)}
  .spread{
    position:absolute;left:122px;top:100px;width:998px;height:710px;
    display:grid;grid-template-columns:675px 323px;grid-template-rows:237px 236px 237px;
    box-shadow:0 2px 10px rgba(0,0,0,.25);
  }
  .tour-photo{position:relative;overflow:hidden}
  .tour-photo::after{
    content:"";position:absolute;left:0;right:0;bottom:0;height:45%;
    background:linear-gradient(to bottom,rgba(0,0,0,0),var(--shade));
  }
  .photo-harbour{background:linear-gradient(to bottom,#7fa5d6 0%,#a9c1dc 14%,#8b8f96 22%,#5d6a73 40%,#1d4f9a 58%,#173f86 80%,#0f2a60 100%)}
  .photo-coastal{background:linear-gradient(to bottom,#9eaec0 0%,#c3ccd6 18%,#6c7b74 30%,#4e5a43 45%,#5a5548 55%,#1f3a66 68%,#1a3359 100%)}
  .photo-mountains{background:linear-gradient(to bottom,#b49478 0%,#8e7a60 10%,#3f5a2c 28%,#2f5022 55%,#355a24 75%,#22351a 100%)}
  .tour-caption{
    position:absolute;left:20px;right:16px;bottom:12px;z-index:1;
    display:flex;align-items:flex-end;justify-content:space-between;color:var(--text-white);
  }
  .tour-title{
    font-family:"Roboto Condensed",sans-serif;font-weight:300;font-size:27px;
    text-transform:uppercase;letter-spacing:.2px;line-height:1;
  }
  .tour-price{display:flex;align-items:flex-end;gap:14px}
  .price-amount{font-family:"Roboto Condensed",sans-serif;font-weight:400;font-size:38px;line-height:.9}
  .price-meta{font-family:"Roboto",sans-serif;font-size:13.5px;line-height:1.1;text-transform:none}
  .price-meta span{display:block;text-transform:uppercase}
  .tour-info{
    padding:0 18px;color:var(--text-white);font-family:"Roboto",sans-serif;
    display:flex;flex-direction:column;justify-content:center;
  }
  .info-harbour{background:linear-gradient(160deg,var(--panel-blue-deep),var(--panel-blue));justify-content:flex-start;padding-top:50px}
  .info-coastal{background:linear-gradient(160deg,var(--panel-blue),var(--panel-blue-light));justify-content:flex-start;padding-top:18px}
  .info-mountains{background:linear-gradient(160deg,var(--panel-blue-light),var(--panel-blue));justify-content:flex-start;padding-top:45px}
  .tour-intro{font-style:italic;font-size:10.6px;line-height:1.28;color:var(--text-soft);margin-bottom:14px}
  .stop-list{list-style:none}
  .stop-list li{display:flex;align-items:center;gap:11px;font-size:12.6px;line-height:16.2px}
  .stop-list svg{width:11px;height:11px;flex:none;fill:var(--text-white)}
</style>
</head>
<body>
<svg width="0" height="0" style="position:absolute">
  <symbol id="plane" viewBox="0 0 24 24"><path d="M21 12.8v-1.6l-8-4.7V2.5a1.5 1.5 0 0 0-3 0v4L2 11.2v1.6l8-2.4v4.8l-2.2 1.6V18l3.7-1 3.7 1v-1.2L13 15.2v-4.8z" transform="rotate(90 12 12)"/></symbol>
</svg>

<main class="spread">
  <section class="tour-photo photo-harbour" role="img" aria-label="Aerial daylight view of the city skyline, harbour and arch bridge">
    <div class="tour-caption">
      <h2 class="tour-title">Sydney Harbour Scenic</h2>
      <div class="tour-price"><span class="price-amount">$560</span><span class="price-meta">per aircraft<span>1 hour 20 mins</span></span></div>
    </div>
  </section>
  <section class="tour-info info-harbour">
    <p class="tour-intro">Our most popular flight – showcasing spectacular Sydney Harbour – including the The Harbour Bridge and the world famous Opera House</p>
    <ul class="stop-list">
      <li><svg><use href="#plane"/></svg>Parramatta City</li>
      <li><svg><use href="#plane"/></svg>Hornsby</li>
      <li><svg><use href="#plane"/></svg>Bahai Temple</li>
      <li><svg><use href="#plane"/></svg>Long Reef</li>
      <li><svg><use href="#plane"/></svg>Habour Bridge &amp; Opera House</li>
      <li><svg><use href="#plane"/></svg>Manly</li>
    </ul>
  </section>

  <section class="tour-photo photo-coastal" role="img" aria-label="Aerial view of sandstone coastal cliffs meeting the ocean">
    <div class="tour-caption">
      <h2 class="tour-title">Sydney Coastal</h2>
      <div class="tour-price"><span class="price-amount">$560</span><span class="price-meta">per aircraft<span>1 hour 20 mins</span></span></div>
    </div>
  </section>
  <section class="tour-info info-coastal">
    <p class="tour-intro">This is one of our most popular scenic tours because it showcases Sydneys magnificent coastline and world famous beaches. The Sydney coastal flight takes you past many well known coastal landmarks and beaches such as Maroubra Beach, Coogee Beach, famous Bondi Beach, and Manly Beach.</p>
    <ul class="stop-list">
      <li><svg><use href="#plane"/></svg>Campbelltown.</li>
      <li><svg><use href="#plane"/></svg>Stanwell Park.</li>
      <li><svg><use href="#plane"/></svg>Entrance of Port Hacking.</li>
      <li><svg><use href="#plane"/></svg>Entrance of Botany Bay.</li>
      <li><svg><use href="#plane"/></svg>Sydney Beaches</li>
      <li><svg><use href="#plane"/></svg>Sydney Heads</li>
      <li><svg><use href="#plane"/></svg>Long Reef</li>
    </ul>
  </section>

  <section class="tour-photo photo-mountains" role="img" aria-label="Forested valley below sandstone cliffs and rock pillars in the Blue Mountains">
    <div class="tour-caption">
      <h2 class="tour-title">Blue Mountains</h2>
      <div class="tour-price"><span class="price-amount">$475</span><span class="price-meta">per aircraft<span>1 hour 10 mins</span></span></div>
    </div>
  </section>
  <section class="tour-info info-mountains">
    <p class="tour-intro">Discover the expansive views of Sydney’s west with a flight over the famous Blue Mountains – showcasing Katoomba and the Three Sister. On the return flight we fly over one of Sydney’s most important resources – Warragamba Dam. A magnificent flight that you will</p>
    <ul class="stop-list">
      <li><svg><use href="#plane"/></svg>Katoomba.</li>
      <li><svg><use href="#plane"/></svg>The Three Sisters.</li>
      <li><svg><use href="#plane"/></svg>Warragamba Dam</li>
      <li><svg><use href="#plane"/></svg>Prospect Reservoir.</li>
    </ul>
  </section>
</main>
</body>
</html>
```